Brackwell Exteriors Needs a New Website!

We are an exteriors company specializing in vinyl siding, Corwin Maddox siding, aluminum soffit/fascia, trough. We do new construction work as well as renovations. We also build detached garages.
You can view our current website at www.brackwellfabricators.ca
I want to completely overhaul the website.
Our services are different now as we no longer do new home construction as well as we do not do the snow clearing.
I want to focus on 2 things in particular on the website:

1/ Exterior renovations

2/ Detached Garage construction.

I have included our logo in the attached files to use as well.

Some features we would like:

1/ Be able to easily attach a video from Clipverse/Reelio to highlight a product or service
2/ Quick chat or contact button that we can talk to a potential client quickly
3/ Meet the Team page that is interesting and fresh
4/ Place for us to put in helpful exterior tips/suggestions for homeowners.

Content is not important, but looking for the best design that will attract people once they click on our page and want to renovate with us.

Target Market(s)

People looking for renovations on their home, people looking to build a detached garage.

Industry/Entity Type

Residential Construction

Number of Pages Required

5+ page

Font styles to use
Sans Serif

Requirements
Must have
• Fresh and exciting home page.

Simple design. Don't want it over complicated or too much information to confuse the potential client.

Easy way to contact us.

Meet the team page that instills confidence
Nice to have
• Colour of website to go off our logo. Doesn't need to be an exact match, but something that goes well with our blue and grey.

```html
<!DOCTYPE html>
<html lang="en">
<head>
<meta charset="utf-8">
<title>Brackwell Builders Ltd</title>
<link rel="stylesheet" href="https://fonts.googleapis.com/css2?family=Montserrat:wght@500;600&family=Arimo:wght@400;700&display=swap">
<style>
:root{
  --blue:#0c6fc7;
  --blue-dark:#0a4f91;
  --ink:#1b1b1b;
  --text:#333;
  --grey:#b9bcc0;
  --line:#cfd2d6;
  --band:#f3f4f6;
  --white:#fff;
}
*{box-sizing:border-box;margin:0;padding:0}
html,body{width:1200px;height:4386px;overflow:hidden;background:var(--white)}
body{font-family:"Arimo",Arial,sans-serif;color:var(--text);position:relative}
.abs{position:absolute}
.head{font-family:"Montserrat",Arial,sans-serif;font-weight:500;color:var(--ink);text-transform:uppercase}
/* header */
.site-header{left:0;top:0;width:1200px;height:94px;background:var(--white)}
.brand{left:105px;top:12px;display:flex;align-items:center;gap:10px}
.brand-mark{width:70px;height:70px;border-radius:50%;border:6px solid var(--blue-dark)}
.brand-name{font-family:"Montserrat",sans-serif;font-weight:600;font-size:30px;color:var(--blue);line-height:1;letter-spacing:.5px}
.nav a{position:absolute;top:34px;font-size:16px;color:var(--ink);text-decoration:none}
.nav .active{color:var(--blue)}
.quote-btn{left:944px;top:22px;width:142px;height:41px;border-radius:21px;background:var(--blue);color:#fff;font-size:16px;display:flex;align-items:center;justify-content:center}
/* hero */
.hero{left:0;top:95px;width:1200px;height:557px;background:linear-gradient(180deg,#8a7f93 0%,#6d7089 35%,#4a5468 70%,#3a3e44 100%)}
.hero-title{left:0;top:200px;width:1200px;text-align:center;font-family:"Montserrat",sans-serif;font-weight:600;font-size:64px;line-height:78px;color:#fff;text-shadow:0 3px 8px rgba(0,0,0,.5)}
.dots{left:565px;top:609px;display:flex;gap:12px}
.dots span{width:14px;height:14px;border-radius:50%;background:#fff}
/* welcome */
.welcome-title{left:111px;top:748px;font-size:29px}
.welcome-title span{color:var(--blue)}
.welcome-text{left:111px;top:803px;width:530px;font-size:16px;line-height:34.3px;color:var(--ink)}
.btn{background:var(--blue);color:#fff;border-radius:22px;display:flex;align-items:center;justify-content:center;font-size:17px}
.video{left:688px;top:754px;width:401px;height:240px;border:1px solid #666;background:linear-gradient(180deg,#a9b7c6 0%,#8f8a82 55%,#6f7a5a 100%)}
.play{left:854px;top:852px;width:48px;height:48px;border-radius:50%;background:var(--blue)}
/* bands */
.band{left:0;width:1200px;background:var(--band);background-image:radial-gradient(#d5d8dc 1.2px,transparent 1.3px);background-size:8px 8px}
.section-title{width:1200px;left:0;text-align:center;font-size:31px}
.service-img{width:272px;height:272px;border-radius:50%;border-bottom:8px solid var(--blue)}
.service-label{width:420px;text-align:center;font-size:22px}
/* why */
.vline{width:1px;background:var(--line)}
.feature{width:300px;text-align:center}
.feature h3{font-family:"Montserrat",sans-serif;font-weight:500;font-size:19px;color:var(--ink);text-transform:uppercase;margin-top:14px}
.feature p{font-size:14.5px;line-height:25.5px;margin:14px auto 0;width:250px;color:var(--ink)}
.arrow{width:36px;height:36px;border-radius:50%;border:1px solid #999;margin:18px auto 0;display:flex;align-items:center;justify-content:center}
.icon{height:56px;display:flex;justify-content:center;align-items:flex-end}
/* team */
.card{width:284px;height:300px;background:#fff;border:1px solid #ccc;box-shadow:0 2px 6px rgba(0,0,0,.15)}
.card-top{position:absolute;left:0;top:0;width:100%;height:60px}
.avatar{position:absolute;left:82px;top:-38px;width:120px;height:120px;border-radius:50%;border:4px solid #fff;background:linear-gradient(180deg,#c8c8c8,#6f6f6f);box-shadow:0 0 0 1px #aaa}
.card h4{position:absolute;top:96px;width:100%;text-align:center;font-family:"Montserrat",sans-serif;font-weight:600;font-size:19px;color:var(--ink)}
.card p{position:absolute;top:140px;left:22px;width:240px;text-align:center;font-size:14.5px;line-height:29px;color:var(--ink)}
.circle-btn{width:38px;height:38px;border-radius:50%;background:#111;display:flex;align-items:center;justify-content:center}
.social{display:flex;gap:10px}
.social span{width:32px;height:32px;border-radius:50%;border:1px solid #aaa;background:#fff;display:flex;align-items:center;justify-content:center}
.social span i{width:10px;height:10px;border-radius:50%;background:#333}
/* featured */
.tile{background:linear-gradient(180deg,#9fb1c6,#5f5a54)}
.tile.warm{background:linear-gradient(180deg,#b0866a,#6b4a35)}
.tile.dusk{background:linear-gradient(180deg,#34507a,#8a6a4a)}
.tile.green{background:linear-gradient(180deg,#c9d6e2,#567060)}
.feature-main{background:linear-gradient(180deg,#4e79a6,#2d4f79);display:flex;align-items:center;justify-content:center;font-family:"Montserrat",sans-serif;font-weight:600;font-size:22px;color:#fff;text-transform:uppercase}
/* footer */
.footer{left:0;top:3870px;width:1200px;height:516px;background:linear-gradient(180deg,#1f6fc0,#0f5aa8)}
.footer-title{font-family:"Montserrat",sans-serif;font-weight:500;font-size:30px;color:#fff}
.contact-icon{width:54px;height:54px;border-radius:50%;background:#fff;display:flex;align-items:center;justify-content:center}
.contact-text{color:#fff;font-size:18px;line-height:34px}
.field{background:#fff;border:1px solid #999;font-size:17px;color:var(--ink);padding:10px 0 0 30px}
.submit{left:756px;top:4252px;width:148px;height:44px;background:#111;color:#fff;font-family:"Montserrat",sans-serif;font-weight:600;font-size:18px;display:flex;align-items:center;justify-content:center}
.foot-social{left:124px;top:4292px;display:flex;gap:25px}
.foot-social span{width:16px;height:16px;border-radius:50%;border:2px solid #fff}
.copyright{left:113px;top:4351px;color:#fff;font-size:12px}
</style>
</head>
<body>

<header class="abs site-header">
  <div class="abs brand"><div class="brand-mark"></div><div class="brand-name">BRACKWELL</div></div>
  <nav class="nav">
    <a class="active" style="left:516px">Home</a>
    <a style="left:605px">Our Services</a>
    <a style="left:745px">Meet the Team</a>
  </nav>
  <svg class="abs" style="left:888px;top:32px" width="24" height="24" viewBox="0 0 24 24" fill="none" stroke="#222" stroke-width="2"><circle cx="10" cy="10" r="7"/><path d="M15 15l7 7"/></svg>
  <div class="abs quote-btn">Request a Quote</div>
</header>

<section class="abs hero" role="img" aria-label="Photo of a modern two-storey house with garage at dusk"></section>
<h1 class="abs hero-title">BRACKWELL<br>BUILDERS LTD</h1>
<div class="abs dots"><span></span><span></span><span></span></div>

<h2 class="abs head welcome-title">Welcome to <span>Brackwell Builders Ltd</span></h2>
<p class="abs welcome-text">Lorem Ipsum is simply dummy text of the printing and typesetting industry. Lorem Ipsum has been the industry's standard dummy text ever since the 1500s, when an unknown printer took a galley of type and scrambled it to make a type specimen book. It has survived not only five centuries, but also the leap into electronic typesetting, remaining essentially unchanged.</p>
<div class="abs btn" style="left:114px;top:1028px;width:146px;height:43px">READ MORE</div>
<div class="abs video" role="img" aria-label="Video still of a large suburban home"></div>
<div class="abs play"><svg width="48" height="48"><path d="M19 14l15 10-15 10z" fill="#fff"/></svg></div>

<section class="abs band" style="top:1140px;height:477px"></section>
<h2 class="abs head section-title" style="top:1182px">Our Services</h2>
<div class="abs service-img" style="left:259px;top:1249px;background:linear-gradient(180deg,#9cc3ea,#cfd4d6 60%,#6c8a5a)" role="img" aria-label="Modern house exterior renovation"></div>
<div class="abs service-img" style="left:688px;top:1249px;background:linear-gradient(180deg,#505861,#2e3338 60%,#8a8a88)" role="img" aria-label="Dark garage door with stone driveway"></div>
<div class="abs head service-label" style="left:190px;top:1553px">Exterior Renovations</div>
<div class="abs head service-label" style="left:614px;top:1553px">Garage Construction</div>

<h2 class="abs head section-title" style="top:1693px">Why Choose Us?</h2>
<div class="abs vline" style="left:402px;top:1787px;height:592px"></div>
<div class="abs vline" style="left:805px;top:1787px;height:592px"></div>
<div class="abs" style="left:111px;top:2087px;width:978px;height:1px;background:var(--line)"></div>

<div class="abs feature" style="left:90px;top:1805px">
  <div class="icon"><svg width="52" height="50" viewBox="0 0 52 50" fill="var(--blue)"><rect x="2" y="20" width="12" height="28"/><path d="M18 20l10-18c6 0 7 4 6 9l-2 7h14c4 0 5 4 4 7l-5 19c-1 3-3 4-6 4H18z"/></svg></div>
  <h3>Certified Experience</h3><p>Having professionals do the job gives you the confidence that the job will be done right.</p>
  <div class="arrow"><svg width="16" height="14" fill="none" stroke="#222" stroke-width="1.6"><path d="M1 7h13M9 2l5 5-5 5"/></svg></div>
</div>
<div class="abs feature" style="left:450px;top:1805px">
  <div class="icon"><svg width="44" height="46" viewBox="0 0 44 46" fill="var(--blue)"><path d="M4 2h10l4 11-6 5c3 7 8 12 15 15l5-6 11 4v10c0 3-3 5-6 5C19 45 0 26 0 7c0-3 2-5 4-5z"/></svg></div>
  <h3>Superior Communication</h3><p>Having professionals do the job gives you the confidence that the job will be done right.</p>
  <div class="arrow"><svg width="16" height="14" fill="none" stroke="#222" stroke-width="1.6"><path d="M1 7h13M9 2l5 5-5 5"/></svg></div>
</div>
<div class="abs feature" style="left:826px;top:1805px">
  <div class="icon"><svg width="66" height="66" viewBox="0 0 66 66"><circle cx="40" cy="20" r="19" fill="var(--blue)"/><text x="40" y="28" font-size="22" text-anchor="middle" fill="#fff" font-family="Arimo">%</text><path d="M2 46h10v18H2zM14 50c8-4 16-4 24 0h10c3 0 3 5 0 5H32m-18 6c14 3 26 1 38-10" fill="none" stroke="var(--blue)" stroke-width="5"/></svg></div>
  <h3>Competitive Pricing</h3><p>Having professionals do the job gives you the confidence that the job will be done right.</p>
  <div class="arrow"><svg width="16" height="14" fill="none" stroke="#222" stroke-width="1.6"><path d="M1 7h13M9 2l5 5-5 5"/></svg></div>
</div>

<div class="abs feature" style="left:86px;top:2105px">
  <div class="icon" style="height:72px"><svg width="72" height="72" viewBox="0 0 72 72" fill="none" stroke="var(--blue)" stroke-width="4"><circle cx="36" cy="16" r="12"/><path d="M14 52c0-14 10-22 22-22s22 8 22 22"/><path d="M14 56l3 6 6 1-5 4 1 6-5-3-5 3 1-6-5-4 6-1zM36 54l3 6 6 1-5 4 1 6-5-3-5 3 1-6-5-4 6-1zM58 56l3 6 6 1-5 4 1 6-5-3-5 3 1-6-5-4 6-1z" fill="var(--blue)" stroke="none"/></svg></div>
  <h3>Guaranteed Satisfaction</h3><p>Having professionals do the job gives you the confidence that the job will be done right.</p>
  <div class="arrow"><svg width="16" height="14" fill="none" stroke="#222" stroke-width="1.6"><path d="M1 7h13M9 2l5 5-5 5"/></svg></div>
</div>
<div class="abs feature" style="left:450px;top:2105px">
  <div class="icon" style="height:72px"><svg width="44" height="56" viewBox="0 0 44 56" fill="var(--blue)"><rect x="2" y="2" width="5" height="54"/><path d="M7 4c12-6 20 6 34 0v24c-14 6-22-6-34 0z"/></svg></div>
  <h3>Superior Communication</h3><p>Having professionals do the job gives you the confidence that the job will be done right.</p>
  <div class="arrow"><svg width="16" height="14" fill="none" stroke="#222" stroke-width="1.6"><path d="M1 7h13M9 2l5 5-5 5"/></svg></div>
</div>
<div class="abs feature" style="left:826px;top:2105px">
  <div class="icon" style="height:72px"><svg width="58" height="58" viewBox="0 0 58 58" fill="none" stroke="var(--blue)" stroke-width="6" stroke-linecap="round"><path d="M8 50L40 18M42 8l8 8M36 6c6-4 12 0 14 4M50 50L18 18M10 6l8 8-4 4-8-8z"/></svg></div>
  <h3>Unrivalled Quality</h3><p>Having professionals do the job gives you the confidence that the job will be done right.</p>
  <div class="arrow"><svg width="16" height="14" fill="none" stroke="#222" stroke-width="1.6"><path d="M1 7h13M9 2l5 5-5 5"/></svg></div>
</div>

<section class="abs band" style="top:2493px;height:565px"></section>
<h2 class="abs section-title" style="top:2540px;font-family:'Montserrat',sans-serif;font-weight:500;font-size:35px;color:var(--ink)">Our Team</h2>

<div class="abs card" style="left:128px;top:2672px">
  <svg class="card-top" viewBox="0 0 284 60" preserveAspectRatio="none"><path d="M0 0h70c10 40 40 50 72 50s62-10 72-50h70L262 0C250 34 200 58 142 58S34 34 22 0z" fill="var(--blue)"/></svg>
  <div class="avatar" role="img" aria-label="Team member portrait"></div>
  <h4>Name</h4><p>Lorem ipsum dolor sit amet, consectetur adipiscing elit, sed do eiusmod tempor.</p>
</div>
<div class="abs card" style="left:460px;top:2672px">
  <svg class="card-top" viewBox="0 0 284 60" preserveAspectRatio="none"><path d="M0 0h70c10 40 40 50 72 50s62-10 72-50h70L262 0C250 34 200 58 142 58S34 34 22 0z" fill="var(--blue)"/></svg>
  <div class="avatar" role="img" aria-label="Team member portrait"></div>
  <h4>Name</h4><p>Lorem ipsum dolor sit amet, consectetur adipiscing elit, sed do eiusmod tempor .</p>
  <div class="social" style="position:absolute;left:74px;top:277px"><span><i></i></span><span><i></i></span><span><i></i></span></div>
</div>
<div class="abs card" style="left:795px;top:2672px">
  <svg class="card-top" viewBox="0 0 284 60" preserveAspectRatio="none"><path d="M0 0h70c10 40 40 50 72 50s62-10 72-50h70L262 0C250 34 200 58 142 58S34 34 22 0z" fill="var(--blue)"/></svg>
  <div class="avatar" role="img" aria-label="Team member portrait"></div>
  <h4>Name</h4><p>Lorem ipsum dolor sit amet, consectetur adipiscing elit, sed do eiusmod tempor .</p>
</div>
<div class="abs circle-btn" style="left:63px;top:2834px"><svg width="14" height="14" fill="none" stroke="#fff" stroke-width="2.2"><path d="M10 1L4 7l6 6"/></svg></div>
<div class="abs circle-btn" style="left:1101px;top:2834px"><svg width="14" height="14" fill="none" stroke="#fff" stroke-width="2.2"><path d="M4 1l6 6-6 6"/></svg></div>

<h2 class="abs head section-title" style="top:3150px;font-size:35px">Featured Work</h2>
<div class="abs feature-main" style="left:111px;top:3254px;width:478px;height:325px" role="img" aria-label="House under construction with blue overlay">Current Custom Home Build</div>
<div class="abs tile" style="left:609px;top:3254px;width:230px;height:150px" role="img" aria-label="Two-storey shingled home"></div>
<div class="abs tile warm" style="left:860px;top:3254px;width:229px;height:150px" role="img" aria-label="Timber framing interior"></div>
<div class="abs tile green" style="left:609px;top:3430px;width:230px;height:149px" role="img" aria-label="Modern home with pool"></div>
<div class="abs tile" style="left:860px;top:3430px;width:229px;height:149px" role="img" aria-label="White suburban house"></div>
<div class="abs tile warm" style="left:107px;top:3602px;width:228px;height:149px" role="img" aria-label="Framed staircase"></div>
<div class="abs tile" style="left:357px;top:3602px;width:229px;height:149px" role="img" aria-label="Siding installation on house wall"></div>
<div class="abs tile" style="left:609px;top:3602px;width:230px;height:149px" role="img" aria-label="Grey shingled home"></div>
<div class="abs tile dusk" style="left:860px;top:3602px;width:229px;height:149px" role="img" aria-label="Lit house at dusk"></div>

<footer class="abs footer"></footer>
<h2 class="abs footer-title" style="left:119px;top:3930px">Contact Us</h2>
<h2 class="abs footer-title" style="left:742px;top:3930px">Get In Touch</h2>
<div class="abs contact-icon" style="left:116px;top:4024px"><svg width="22" height="28" viewBox="0 0 22 28" fill="#222"><path d="M11 0C5 0 0 5 0 11c0 8 11 17 11 17s11-9 11-17C22 5 17 0 11 0zm0 15a4 4 0 110-8 4 4 0 010 8z"/></svg></div>
<div class="abs contact-icon" style="left:116px;top:4116px"><svg width="24" height="24" viewBox="0 0 44 46" fill="#222"><path d="M4 2h10l4 11-6 5c3 7 8 12 15 15l5-6 11 4v10c0 3-3 5-6 5C19 45 0 26 0 7c0-3 2-5 4-5z"/></svg></div>
<div class="abs contact-icon" style="left:116px;top:4203px"><svg width="24" height="18" viewBox="0 0 24 18"><rect width="24" height="18" rx="2" fill="#222"/><path d="M1 2l11 8 11-8" fill="none" stroke="#fff" stroke-width="1.6"/></svg></div>
<p class="abs contact-text" style="left:195px;top:4022px">2410 Larkfield Row,<br>Elmhurst, CA</p>
<p class="abs contact-text" style="left:195px;top:4126px">Tel:&nbsp; (555) 014-2276</p>
<p class="abs contact-text" style="left:193px;top:4213px">Email:info@brackwellbuilders.com</p>

<div class="abs field" style="left:577px;top:4018px;width:245px;height:43px">First Name</div>
<div class="abs field" style="left:834px;top:4018px;width:245px;height:43px;padding-left:22px">Last Name</div>
<div class="abs field" style="left:577px;top:4088px;width:245px;height:44px">Phone</div>
<div class="abs field" style="left:834px;top:4088px;width:245px;height:44px;padding-left:22px">Email</div>
<div class="abs field" style="left:577px;top:4155px;width:502px;height:66px">Message</div>
<div class="abs submit">SUBMIT</div>
<div class="abs foot-social"><span></span><span></span><span></span><span></span><span></span></div>
<p class="abs copyright">Copyrights © 2020 Copyrights Company Name | All Rights Reserved</p>

</body>
</html>
```